Real estate business card

I need a business card for my real estate company. I help clients buy and sell properties. I would like to keep the design very simple and professional. I would like the design to convey professionalism, safety and trust. I prefer no graphics but a simple logo design would be nice if that is part of what you do.
Updates

Please keep the designs simple. No high-rise buildings please. 

Project Deadline Extended
Reason: My design has not been finalized.

Target Market(s)

Age group 30-60 mostly affluent

Industry/Entity Type

Real Estate

Contact Information for Business Card

Velmont Realtors
Gregory Velmont, Broker
4815 Brindle Ave. #263, La Crescenta, CA 91206

Requirements
Nice to have
• Logo can be combination of my initials GV or just Z or a simple geometric shape? Please see "Desig Ideas" attachment. No pics of houses or shaking hands, dollar bills, $, %, etc...
Please use fonts similar to Helvetica for a clean, modern look (think Northern European design, simple, clean yet bold)

Also use font colors such as blue, grey in different shades. Use pastel colors if better.

```html
<!DOCTYPE html>
<html lang="en">
<head>
<meta charset="utf-8">
<title>Velmont Realtors – Business Card</title>
<link href="https://fonts.googleapis.com/css2?family=Inter:wght@300;400&display=swap" rel="stylesheet">
<style>
  :root {
    --page-bg: #1c1f21;
    --card-grey-light: #7a7a7a;
    --card-grey-mid: #4e4e4e;
    --card-grey-dark: #363636;
    --band-blue-light: #12c8ff;
    --band-blue: #0a9cf0;
    --band-blue-deep: #0060e6;
    --corner-grey: #3c3c3c;
    --text-white: #ffffff;
    --text-soft: #d9d9d9;
  }
  html, body {
    margin: 0;
    padding: 0;
    width: 1200px;
    height: 1164px;
    overflow: hidden;
    background: var(--page-bg);
    font-family: "Inter", "Helvetica Neue", Arial, sans-serif;
  }
  .stage {
    width: 1200px;
    height: 1164px;
    display: flex;
    align-items: center;
    justify-content: center;
  }
  .business-card {
    position: relative;
    width: 1000px;
    height: 572px;
    overflow: hidden;
    background: radial-gradient(circle at 58% 42%, var(--card-grey-light) 0%, var(--card-grey-mid) 38%, var(--card-grey-dark) 100%);
    box-shadow: 0 20px 50px rgba(0,0,0,0.55);
  }
  .brand-band {
    position: absolute;
    inset: 0;
    width: 100%;
    height: 100%;
  }
  .brand-name {
    position: absolute;
    left: 62px;
    top: 300px;
    transform: rotate(-55deg);
    transform-origin: left center;
    color: var(--text-white);
    font-weight: 400;
    font-size: 40px;
    letter-spacing: 1px;
    white-space: nowrap;
    display: flex;
    align-items: center;
    gap: 14px;
  }
  .brand-square {
    width: 26px;
    height: 26px;
    background: var(--text-white);
  }
  .contact-block {
    position: absolute;
    right: 56px;
    top: 52px;
    text-align: right;
    color: var(--text-white);
    font-weight: 300;
  }
  .company-name { font-size: 46px; margin: 0 0 10px; font-weight: 300; }
  .person-name { font-size: 36px; margin: 0; font-weight: 300; }
  .person-title { font-size: 28px; margin: 4px 0 34px; color: var(--text-soft); }
  .phone { font-size: 28px; margin: 0 0 70px; color: var(--text-soft); }
  .address { font-size: 27px; margin: 0; line-height: 1.45; color: var(--text-soft); font-style: normal; }
  .license {
    position: absolute;
    left: 272px;
    bottom: 40px;
    font-size: 27px;
    font-weight: 300;
    color: var(--text-soft);
  }
</style>
</head>
<body>
  <main class="stage">
    <section class="business-card">
      <svg class="brand-band" viewBox="0 0 1000 572" preserveAspectRatio="none" aria-hidden="true">
        <defs>
          <linearGradient id="bandGradient" x1="0" y1="0" x2="1" y2="1">
            <stop offset="0" stop-color="var(--band-blue-light)"/>
            <stop offset="0.55" stop-color="var(--band-blue)"/>
            <stop offset="1" stop-color="var(--band-blue-deep)"/>
          </linearGradient>
        </defs>
        <polygon points="0,0 130,0 0,160" fill="var(--corner-grey)"/>
        <polygon points="130,0 620,0 225,572 0,572 0,160" fill="url(#bandGradient)"/>
      </svg>

      <div class="brand-name">
        <span class="brand-square"></span>
        <span>GV REAL ESTATE</span>
      </div>

      <div class="contact-block">
        <p class="company-name">Velmont Realtors</p>
        <p class="person-name">Gregory Velmont</p>
        <p class="person-title">Broker</p>
        <p class="phone">(818) 555-0142</p>
        <address class="address">4815 Brindle Ave. #263,<br>La Crescenta, CA 91206</address>
      </div>

      <p class="license">CA BRE 01937845</p>
    </section>
  </main>
</body>
</html>
```